Drinking and Driving course for the courts

Sophisitcated tri-fold brochure seen by judges, lawyers etc. People taking this course have been charged with drinking and driving (alcohol). Should be classy and upmarket. Please be creative like original brochure. Please use exact wording and in same order as brochure. Also please keep in approximately same place on brochure. Spelling and grammar should be exactly same as this document is already proof-read and checked by experts.

Target Market(s)

Judges, lawyers, court system.

Industry/Entity Type

Legal

Font styles to use
Serif

Requirements
Must have
• Creative and classy. Can look similar or same as original brochure. Should have pciture/graphic of car keys and drink
Nice to have
• A background graphic like in original brochure comes across very well. Subtle etc.
Should not have
• Does not need to have pictures of vehicles/cars. Definitely no brand names of cars or alcohol labels (or any kind).

```html
<!DOCTYPE html>
<html lang="en">
<head>
<meta charset="utf-8">
<title>Sobering Truth – Brochure Cover Options</title>
<link rel="stylesheet" href="https://fonts.googleapis.com/css2?family=Montserrat:wght@400;600;700&family=Special+Elite&family=Oswald:wght@500;700&family=Rubik+Distressed&family=Open+Sans:wght@600;700&display=swap">
<style>
  :root {
    --board: #e1e1e2;
    --label: #1a1a1a;
    --cover-black: #0b0908;
    --gold: #e8bd3a;
    --amber: #d08a1c;
    --navy: #1d3270;
    --white: #ffffff;
  }
  * { box-sizing: border-box; margin: 0; padding: 0; }
  html, body { width: 1200px; height: 1085px; overflow: hidden; }
  body { background: var(--board); position: relative; font-family: "Montserrat", sans-serif; }

  .option-label {
    position: absolute; top: 100px; width: 340px;
    text-align: center; font-weight: 700; font-size: 23px;
    letter-spacing: 1.5px; color: var(--label);
  }
  .cover {
    position: absolute; top: 160px; width: 340px; height: 788px;
    background: var(--white); overflow: hidden;
    box-shadow: 8px 8px 14px rgba(0,0,0,0.45);
  }
  .cover-dark {
    position: absolute; inset: 0 0 auto 0; height: 600px;
    background: linear-gradient(to bottom, #050404 0, #050404 95px, var(--cover-black) 96px, var(--cover-black) 380px, #1a1816 430px, #6d6b68 490px, #e8e8e8 560px, var(--white) 600px);
  }
  .hero-photo {
    position: absolute; left: 20px; top: 350px; width: 300px; height: 230px;
    background:
      radial-gradient(ellipse 70px 75px at 195px 85px, rgba(232,165,40,0.95), rgba(208,138,28,0.5) 60%, transparent 100%),
      radial-gradient(ellipse 110px 28px at 110px 195px, rgba(30,30,30,0.85), transparent 100%);
  }
  .headline { position: absolute; left: 0; width: 100%; text-align: center; color: var(--gold); line-height: 1; font-weight: 400; }
  .headline .title-top { display: block; white-space: nowrap; }
  .headline .title-bottom { display: block; font-family: "Montserrat", sans-serif; font-weight: 600; font-size: 58px; letter-spacing: 2px; margin-top: -4px; }
  .v1 .title-top { font-family: "Special Elite", serif; font-size: 48px; letter-spacing: -1px; }
  .v2 .title-top { font-family: "Oswald", sans-serif; font-weight: 500; font-size: 60px; transform: scaleX(0.82); }
  .v3 .title-top { font-family: "Rubik Distressed", sans-serif; font-size: 50px; transform: scaleX(0.8); }
  .v2 .title-bottom, .v3 .title-bottom { margin-top: -12px; }

  .course-line {
    position: absolute; left: 0; width: 100%; text-align: center;
    color: var(--gold); font-size: 13px; line-height: 18px; letter-spacing: 0.6px;
  }
  .course-line strong { font-weight: 700; }

  .school { position: absolute; left: 0; top: 610px; width: 100%; text-align: center; color: var(--navy); }
  .school-name { font-family: "Oswald", sans-serif; font-weight: 700; font-size: 22px; letter-spacing: -0.3px; }
  .tagline { font-family: "Open Sans", sans-serif; font-weight: 600; font-size: 11px; margin-top: 2px; }
  .school-mark { display: block; margin: 14px auto 0; width: 22px; height: 22px; border-radius: 50%; background: var(--navy); }
  .services { margin-top: 24px; font-family: "Open Sans", sans-serif; font-weight: 700; font-size: 10.5px; line-height: 15px; }
</style>
</head>
<body>
  <div class="option-label" style="left:59px">OPTION 1</div>
  <div class="option-label" style="left:430px">OPTION 2</div>
  <div class="option-label" style="left:814px">OPTION 3</div>

  <article class="cover v1" style="left:59px">
    <div class="cover-dark"></div>
    <div class="hero-photo" role="img" aria-label="Glass of whisky on ice beside a set of car keys on a white surface"></div>
    <h1 class="headline" style="top:118px"><span class="title-top">SOBERING</span><span class="title-bottom">TRUTH</span></h1>
    <p class="course-line" style="top:246px"><strong>A 1-DAY EDUCATIONAL COURSE</strong><br>FOR THOSE CHARGED WITH<br>DRINKING AND DRIVING</p>
    <div class="school">
      <div class="school-name">Safe Lane Driving School</div>
      <div class="tagline">Building careful drivers...for good!</div>
      <span class="school-mark"></span>
      <div class="services">For all your G License needs!<br>Beginner, Rehabilitation &amp; Remedial</div>
    </div>
  </article>

  <article class="cover v2" style="left:430px">
    <div class="cover-dark"></div>
    <div class="hero-photo" role="img" aria-label="Glass of whisky on ice beside a set of car keys on a white surface"></div>
    <h1 class="headline" style="top:118px"><span class="title-top">SOBERING</span><span class="title-bottom">TRUTH</span></h1>
    <p class="course-line" style="top:256px"><strong>A 1-DAY EDUCATIONAL COURSE</strong><br>FOR THOSE CHARGED WITH<br>DRINKING AND DRIVING</p>
    <div class="school">
      <div class="school-name">Safe Lane Driving School</div>
      <div class="tagline">Building careful drivers...for good!</div>
      <span class="school-mark"></span>
      <div class="services">For all your G License needs!<br>Beginner, Rehabilitation &amp; Remedial</div>
    </div>
  </article>

  <article class="cover v3" style="left:814px">
    <div class="cover-dark"></div>
    <div class="hero-photo" role="img" aria-label="Glass of whisky on ice beside a set of car keys on a white surface"></div>
    <h1 class="headline" style="top:116px"><span class="title-top">SOBERING</span><span class="title-bottom">TRUTH</span></h1>
    <p class="course-line" style="top:256px"><strong>A 1-DAY EDUCATIONAL COURSE</strong><br>FOR THOSE CHARGED WITH<br>DRINKING AND DRIVING</p>
    <div class="school">
      <div class="school-name">Safe Lane Driving School</div>
      <div class="tagline">Building careful drivers...for good!</div>
      <span class="school-mark"></span>
      <div class="services">For all your G License needs!<br>Beginner, Rehabilitation &amp; Remedial</div>
    </div>
  </article>
</body>
</html>
```